Lantern Hollow Brewing Company New Website with Food Ordering

We need a wordpress-based website for a local brewery & pizza kitchen. The final design will have 6 primary pages: home page, order pizza, our beers, visit us, about us, merch store. The website must integrate with tillpoint for kitchens for online ordering for takeout and delivery. It will also a feature a selection of beers and help customers navigate to the brewery and find hours of operation. The existing website is lanternhollowbrew.example. This is a very old website.

Industry/Entity Type

Brewery and food service

Coding

Coded - Design and coding required

Number of Pages Required

5+ page

Font styles to use
Sans Serif

Requirements
Must have
• ability to integrate seamlessly with tillpoint for kitchens, 21+ age gate
Nice to have
• see attached pdf

```html
<!DOCTYPE html>
<html lang="en">
<head>
<meta charset="utf-8">
<title>Lantern Hollow Brewing Company</title>
<link rel="stylesheet" href="https://fonts.googleapis.com/css2?family=Montserrat:wght@400;500;600;700;800&display=swap">
<style>
  :root {
    --red: #c8133a;
    --red-deep: #a80f30;
    --ink: #1a1a1a;
    --black: #000;
    --orange: #f9a533;
    --white: #fff;
    --pink: #f9bfcc;
    --grey-tile: #e0e0e0;
    --text: #222;
  }
  * { margin: 0; padding: 0; box-sizing: border-box; }
  html, body { width: 1200px; height: 2274px; overflow: hidden; }
  body { font-family: "Montserrat", sans-serif; color: var(--text); background: var(--white); position: relative; }
  .abs { position: absolute; }

  /* header */
  .brand-name { left: 111px; top: 40px; font-weight: 800; font-size: 22px; line-height: 1.15; color: var(--red); width: 200px; }
  .contact { top: 22px; display: flex; align-items: center; gap: 8px; white-space: nowrap; }
  .contact .dot { width: 31px; height: 31px; border-radius: 50%; background: var(--red); display: flex; align-items: center; justify-content: center; flex: none; }
  .contact small { display: block; font-size: 8px; color: #555; letter-spacing: .3px; }
  .contact strong { display: block; font-size: 14px; font-weight: 600; color: var(--ink); }
  .social { display: flex; gap: 12px; }
  .social span { width: 31px; height: 31px; border-radius: 50%; background: var(--red); display: flex; align-items: center; justify-content: center; }
  .social span::before { content: ""; width: 10px; height: 10px; border-radius: 50%; border: 2px solid var(--white); }
  .main-nav { left: 448px; top: 75px; width: 752px; height: 42px; }
  .main-nav ul { position: absolute; left: 76px; top: 0; display: flex; gap: 27px; list-style: none; height: 42px; align-items: center; }
  .main-nav li { color: var(--white); font-size: 17px; font-weight: 500; position: relative; }
  .main-nav li.active { font-weight: 700; }
  .main-nav li.active::before { content: ""; position: absolute; left: 0; right: 0; top: -11px; height: 3px; background: var(--red); }

  /* hero */
  .hero-title { left: 110px; top: 232px; font-weight: 700; font-size: 58px; line-height: 71px; color: var(--white); letter-spacing: -.5px; }
  .hero-title .accent { color: var(--orange); }
  .btn { position: absolute; height: 46px; display: flex; align-items: center; justify-content: center; font-size: 16px; font-weight: 600; transform: skewX(-8deg); }
  .btn span { transform: skewX(8deg); }
  .btn-light { background: var(--white); color: var(--ink); border-left: 5px solid var(--orange); border-right: 5px solid var(--orange); }
  .btn-dark { background: var(--black); color: var(--white); border-left: 5px solid var(--orange); border-right: 5px solid var(--orange); }
  .btn-orange { background: var(--orange); color: var(--ink); border-left: 5px solid var(--white); border-right: 5px solid var(--white); }
  .btn-red { background: var(--red); color: var(--white); border-left: 5px solid var(--ink); border-right: 5px solid var(--ink); }

  /* section heading */
  .section-title { left: 0; width: 1200px; display: flex; justify-content: center; align-items: center; gap: 22px; font-weight: 700; font-size: 53px; }
  .dash { width: 40px; height: 10px; position: relative; }
  .dash::before, .dash::after { content: ""; position: absolute; height: 2px; }
  .dash::before { left: 0; right: 0; bottom: 0; }
  .dash::after { top: 0; width: 16px; }
  .dash.left::after { left: 0; } .dash.right::after { right: 0; }
  .on-white .dash::before, .on-white .dash::after { background: var(--ink); }
  .on-red .dash::before, .on-red .dash::after { background: var(--white); }
  .intro { left: 160px; width: 880px; top: 954px; text-align: center; font-size: 16px; line-height: 28px; color: var(--ink); }

  /* menu cards */
  .card { position: absolute; top: 1083px; width: 309px; height: 423px; }
  .card .tile { position: absolute; left: 0; top: 0; width: 309px; height: 125px; }
  .card .dish { position: absolute; left: 40px; top: 52px; width: 230px; height: 185px; border-radius: 10px; background: radial-gradient(ellipse at 50% 45%, #b24a3a, #7a2320 70%, #5a1a16); }
  .card h3 { position: absolute; top: 277px; left: 0; width: 309px; text-align: center; font-size: 18px; font-weight: 700; color: var(--ink); }
  .card p { position: absolute; top: 309px; left: 0; width: 309px; text-align: center; font-size: 14.5px; line-height: 28px; color: #333; }
  .card .actions { position: absolute; top: 384px; left: 0; width: 309px; height: 39px; display: flex; font-size: 15px; }
  .card .actions span { display: flex; align-items: center; justify-content: center; color: var(--white); }
  .card .carryout { width: 153px; background: var(--red); }
  .card .delivery { flex: 1; background: var(--black); }

  /* questions band */
  .call-band { left: 0; top: 1681px; width: 1200px; height: 312px; background: linear-gradient(90deg, var(--red-deep), var(--red) 40%, var(--red) 70%, var(--red-deep)); }
  .call-text { left: 530px; top: 1836px; color: var(--white); white-space: nowrap; }
  .call-text .lead { font-size: 33px; font-weight: 400; line-height: 46px; }
  .call-text .number { font-size: 35px; font-weight: 600; line-height: 44px; }

  /* footer */
  .footer-brand { left: 111px; top: 2068px; font-weight: 800; font-size: 26px; line-height: 1.15; color: var(--red); width: 220px; }
  .footer-nav { right: 114px; top: 2098px; display: flex; gap: 27px; list-style: none; font-size: 17px; font-weight: 500; color: var(--ink); }
  .rule { left: 111px; top: 2205px; width: 978px; height: 1px; background: #bbb; }
  .copyright { left: 0; width: 1200px; top: 2232px; text-align: center; font-size: 16px; font-weight: 500; color: var(--ink); }
</style>
</head>
<body>

<header>
  <div class="abs brand-name">Lantern Hollow</div>
  <div class="abs contact" style="left:440px">
    <span class="dot"><svg width="14" height="14" viewBox="0 0 24 24"><path fill="#fff" d="M6.6 10.8c1.4 2.8 3.8 5.1 6.6 6.6l2.2-2.2c.3-.3.7-.4 1-.2 1.1.4 2.3.6 3.6.6.6 0 1 .4 1 1V20c0 .6-.4 1-1 1C10.6 21 3 13.4 3 4c0-.6.4-1 1-1h3.5c.6 0 1 .4 1 1 0 1.3.2 2.5.6 3.6.1.3 0 .7-.2 1z"/></svg></span>
    <div><small>PHONE</small><strong>+1-555-014-8820</strong></div>
  </div>
  <div class="abs contact" style="left:612px">
    <span class="dot"><svg width="14" height="14" viewBox="0 0 24 24"><path fill="#fff" d="M3 5h18v14H3z"/><path fill="none" stroke="#c8133a" stroke-width="2" d="M3 6l9 7 9-7"/></svg></span>
    <div><small>EMAIL</small><strong>beerME@lanternhollowbrew.example</strong></div>
  </div>
  <div class="abs social" style="left:972px; top:24px" aria-label="Social links"><span></span><span></span><span></span></div>
  <nav class="abs main-nav">
    <svg class="abs" width="752" height="42" style="left:0;top:0"><polygon points="24,0 752,0 752,42 0,42" fill="#231f20"/></svg>
    <ul>
      <li class="active">Home</li><li>The Kitchen</li><li>Our Beers</li><li>Visit Us</li><li>About Us</li><li>Merch</li>
    </ul>
  </nav>
</header>

<section>
  <svg class="abs" width="1200" height="680" style="left:0;top:117px">
    <defs>
      <linearGradient id="heroRed" x1="0" y1="0" x2="1" y2="1">
        <stop offset="0" stop-color="#c8163d"/><stop offset="1" stop-color="#b8112f"/>
      </linearGradient>
      <radialGradient id="pizzaTone" cx="0.6" cy="0.45" r="0.7">
        <stop offset="0" stop-color="#d4652d"/><stop offset="0.55" stop-color="#a8482a"/><stop offset="1" stop-color="#5e4630"/>
      </radialGradient>
    </defs>
    <rect width="1200" height="640" fill="url(#heroRed)"/>
    <polygon points="556,0 1200,0 1200,540 710,620" fill="url(#pizzaTone)" role="img" aria-label="Photo of a square pepperoni and mushroom pizza in a pan on a wooden board"/>
    <polygon points="0,550 600,625 1200,540 1200,550 600,672 0,570" fill="#000"/>
    <polygon points="0,570 600,672 1200,550 1200,680 0,680" fill="#fff"/>
  </svg>
  <div class="abs" role="img" aria-label="Photo of two glasses of beer with foam" style="left:0;top:400px;width:95px;height:340px;background:linear-gradient(180deg,#f3efe6 0,#e9a640 20%,#c9772a 70%,#e8dcc8 100%);border-radius:0 30px 30px 0;opacity:.95"></div>
  <h1 class="abs hero-title">Square pizza <span class="accent">&amp;</span><br>great beer in<br><span class="accent">Portland</span>,Maine</h1>
  <div class="btn btn-light" style="left:113px;top:475px;width:144px"><span>Our Beers</span></div>
  <div class="btn btn-dark" style="left:277px;top:475px;width:164px"><span>Order Pizza</span></div>
  <div class="btn btn-orange" style="left:113px;top:542px;width:133px"><span>About Us</span></div>
  <div class="btn btn-light" style="left:278px;top:542px;width:127px"><span>Visit Us</span></div>
</section>

<section>
  <h2 class="abs section-title on-white" style="top:856px;color:var(--red)"><span class="dash left"></span>Order Pizza<span class="dash right"></span></h2>
  <p class="abs intro">Sed ut perspiciatis unde omnis iste natus error sit voluptatem accusantium doloremque laudantium, totam rem aperiam, eaque ipsa quae ab illo inventore veritatis et quasi architecto beatae vitae dicta sunt explicabo.</p>

  <article class="card" style="left:111px">
    <div class="tile" style="background:var(--pink)"></div>
    <div class="dish" role="img" aria-label="Photo of Detroit-style pepperoni pizza squares"></div>
    <h3>Detroit-style pizza</h3>
    <p>Nemo enim ipsam voluptatem quia<br>voluptas sit aspernatur aut odit</p>
    <div class="actions"><span class="carryout">Order carryout</span><span class="delivery">Order delivery</span></div>
  </article>
  <article class="card" style="left:446px">
    <div class="tile" style="background:var(--grey-tile)"></div>
    <div class="dish" role="img" aria-label="Photo of Detroit-style pepperoni pizza squares"></div>
    <h3>Detroit-style pizza</h3>
    <p>Nemo enim ipsam voluptatem quia<br>voluptas sit aspernatur aut odit</p>
    <div class="actions"><span class="carryout">Order carryout</span><span class="delivery">Order delivery</span></div>
  </article>
  <article class="card" style="left:780px">
    <div class="tile" style="background:var(--pink)"></div>
    <div class="dish" role="img" aria-label="Photo of Detroit-style pepperoni pizza squares"></div>
    <h3>Detroit-style pizza</h3>
    <p>Nemo enim ipsam voluptatem quia<br>voluptas sit aspernatur aut odit</p>
    <div class="actions"><span class="carryout">Order carryout</span><span class="delivery">Order delivery</span></div>
  </article>

  <div class="btn btn-red" style="left:538px;top:1571px;width:182px;height:45px"><span>View Full Menu</span></div>
</section>

<section>
  <div class="abs call-band"></div>
  <div class="abs" role="img" aria-label="Photo of a pan of pizza with two beers" style="left:0;top:1740px;width:330px;height:290px;border-radius:0 40px 40px 0;background:radial-gradient(ellipse at 40% 55%,#e9b868,#c4602f 55%,#2a2222 85%);transform:rotate(-8deg);transform-origin:left center"></div>
  <div class="abs" role="img" aria-label="Photo of stacked kraft pizza boxes" style="left:880px;top:1745px;width:300px;height:310px;background:linear-gradient(160deg,#d9b58a,#b98e60 60%,#8f6b45);clip-path:polygon(30% 0,100% 18%,100% 75%,60% 100%,0 70%,0 30%)"></div>
  <h2 class="abs section-title on-red" style="top:1724px;color:var(--white)"><span class="dash left"></span>Questions?<span class="dash right"></span></h2>
  <svg class="abs" width="70" height="70" style="left:425px;top:1841px" viewBox="0 0 70 70">
    <circle cx="35" cy="35" r="32" fill="none" stroke="#fff" stroke-width="3"/>
    <path d="M24 20c2-2 4-1 5 1l3 6c1 2 0 3-1 4l-2 2c2 5 6 9 11 11l2-2c1-1 3-2 4-1l6 3c2 1 3 3 1 5l-3 3c-3 3-10 1-17-6s-9-14-6-17z" fill="none" stroke="#fff" stroke-width="2.5" stroke-linejoin="round"/>
  </svg>
  <div class="abs call-text">
    <div class="lead">Give us a call</div>
    <div class="number">+1-555-014-8820</div>
  </div>
</section>

<footer>
  <div class="abs footer-brand">Lantern Hollow</div>
  <ul class="abs footer-nav"><li>Home</li><li>The Kitchen</li><li>Our Beers</li><li>Visit Us</li><li>About Us</li><li>Merch</li></ul>
  <div class="abs social" style="left:972px; top:2144px" aria-label="Social links"><span></span><span></span><span></span></div>
  <div class="abs rule"></div>
  <p class="abs copyright">2022 Lantern Hollow Brew. All Rights Reserved.</p>
</footer>

</body>
</html>
```